Quillbrookes websites redesign

Www.quill-brookes.com needs to be redesigned along with updations. The incremental material will be provided for the updations. We are looking for complete redesign of the pages with the new content. The complete write up will be provided soon

Target Market(s)

Global

Coding

Coded - Design and coding required

Number of Pages Required

5+ page

Requirements
Must have
• A clean and slick design for the Consulting.
Should not have
• Too many pictures which reduces the speed of the site

```html
<!DOCTYPE html>
<html lang="en">
<head>
<meta charset="utf-8">
<title>Quillbrookes</title>
<link href="https://fonts.googleapis.com/css2?family=Lato:wght@400;700&display=swap" rel="stylesheet">
<style>
:root{
  --blue:#37a6cf;
  --dark:#1f1f1f;
  --ink:#222;
  --white:#fff;
  --line:#e2e2e2;
}
*{margin:0;padding:0;box-sizing:border-box}
html,body{width:766px;height:1200px;overflow:hidden}
body{font-family:'Lato',sans-serif;color:var(--ink);background:var(--white);position:relative}
.hero{position:absolute;left:0;top:0;width:766px;height:507px;background:radial-gradient(ellipse at 45% 40%,#6a6c70 0%,#3d3f43 55%,#26282b 100%)}
.brand{position:absolute;left:30px;top:0;width:207px;height:52px;background:#f2f2f2;display:flex;align-items:center;padding-left:14px;gap:10px}
.brand-mark{width:22px;height:22px;border-radius:50%;background:#1f3a5a}
.brand-name{font-size:22px;color:#1f3a5a;font-weight:400}
.nav{position:absolute;left:305px;top:0;display:flex;height:52px}
.nav a{color:var(--white);font-size:8.5px;text-decoration:none;height:52px;display:flex;align-items:center;padding:0 11px;margin-right:8px}
.nav a.active{background:var(--blue);margin-right:10px}
.nav-rule{position:absolute;left:305px;top:52px;width:461px;height:1px;background:rgba(255,255,255,.35)}
.hero-title{position:absolute;left:0;width:766px;top:192px;text-align:center;color:var(--white);font-size:36px;font-weight:700;letter-spacing:-.5px}
.hero-title span,.section-title span{color:var(--blue)}
.hero-rule{position:absolute;left:143px;top:238px;width:494px;height:1px;background:var(--white)}
.hero-sub{position:absolute;left:180px;top:243px;width:420px;text-align:center;color:var(--white);font-size:12px;line-height:18px}
.arrow{position:absolute;top:200px;width:26px;height:26px;border:1.5px solid var(--white);border-radius:50%}
.arrow svg{position:absolute;left:7px;top:7px}
.track{position:absolute;left:0;top:400px;width:766px;height:1px;background:rgba(255,255,255,.8)}
.range{position:absolute;top:357px;width:86px;height:86px;border-radius:50%;border:2px solid var(--white);background:var(--blue);color:var(--white);font-size:14px;display:flex;align-items:center;justify-content:center;box-shadow:0 0 0 1px rgba(0,0,0,.2)}
.welcome{position:absolute;left:0;top:507px;width:766px;height:183px;text-align:center}
.section-title{font-size:24px;font-weight:700;position:absolute;width:100%;top:40px}
.welcome p{position:absolute;top:80px;width:100%;font-size:7px;line-height:14px;color:#333}
.btn{position:absolute;left:342px;top:123px;width:85px;height:21px;background:var(--blue);color:var(--white);font-size:7px;display:flex;align-items:center;justify-content:center}
.cases{position:absolute;left:0;top:690px;width:766px;height:446px;background:var(--dark)}
.cases h2{position:absolute;width:100%;top:22px;text-align:center;color:var(--white);font-size:21px;font-weight:700}
.card{position:absolute;top:78px;width:333px;height:347px;background:var(--white)}
.card.left{left:30px}
.card.right{left:404px;background:var(--blue);color:var(--white)}
.card h3{height:49px;display:flex;align-items:center;justify-content:center;font-weight:400;font-size:14px;color:var(--blue);border-bottom:1px solid var(--blue)}
.card.right h3{color:var(--white);border-bottom-color:rgba(255,255,255,.4)}
.card .icon{display:block;margin:10px auto 0}
.card ul{list-style:none;position:absolute;top:115px;left:18px;right:18px}
.card li{font-size:7.4px;line-height:9px;padding-left:15px;position:relative;margin-bottom:10px;min-height:18px}
.card li svg{position:absolute;left:0;top:0}
.card .more{position:absolute;left:0;top:291px;width:100%;height:24px;background:var(--blue);color:var(--white);font-size:7.5px;display:flex;align-items:center;justify-content:center}
.card.right .more{background:var(--white);color:var(--blue)}
.footer{position:absolute;left:0;top:1136px;width:766px;height:64px}
.footer p{position:absolute;left:34px;top:27px;font-size:7px;color:#333}
.social{position:absolute;right:46px;top:27px;display:flex;gap:16px}
.social i{width:8px;height:8px;border-radius:50%;background:#b5b5b5;display:block}
</style>
</head>
<body>
<header class="hero" role="img" aria-label="Photo of business people working at a desk with laptop, papers and coffee">
  <div class="brand"><span class="brand-mark"></span><span class="brand-name">Quillbrookes</span></div>
  <nav class="nav">
    <a class="active">HOME</a><a>FOUNDER</a><a>CONSULTANCY</a><a>SYSTEM</a><a>CASE STUDIES</a><a>CONTACT US</a>
  </nav>
  <div class="nav-rule"></div>
  <span class="arrow" style="left:32px"><svg width="10" height="10" viewBox="0 0 10 10"><path d="M6.5 1.5 3 5l3.5 3.5" fill="none" stroke="#fff" stroke-width="1.4"/></svg></span>
  <span class="arrow" style="left:711px"><svg width="10" height="10" viewBox="0 0 10 10"><path d="M3.5 1.5 7 5 3.5 8.5" fill="none" stroke="#fff" stroke-width="1.4"/></svg></span>
  <h1 class="hero-title">WELCOME TO <span>QUILLBROOKE</span></h1>
  <div class="hero-rule"></div>
  <p class="hero-sub">Lorem ipsum dolor sit amet, consectetur adipiscing elit, sed do eiusmod tempor incididunt ut labore et dolore magna aliqua</p>
  <div class="track"></div>
  <div class="range" style="left:122px">0 - 250</div>
  <div class="range" style="left:276px">250 - 500</div>
  <div class="range" style="left:423px">500 - 1000</div>
  <div class="range" style="left:568px">&gt; 1000</div>
</header>

<section class="welcome">
  <h2 class="section-title">WELCOME TO <span>QUILLBROOKES</span></h2>
  <p>It is burning. Now it is: get out of the building. To safety. Escape and rescue plans are an important guide and also an essential tool for training people for the right behavior in case of fire.<br>With the professional preparation of escape and rescue plans we contribute our part in ensuring that people with you in case of a fire in the shortest find ways out of the building.</p>
  <span class="btn">READ MORE</span>
</section>

<section class="cases">
  <h2>CASE STUDIES</h2>
  <article class="card left">
    <h3>Structured Financing</h3>
    <svg class="icon" width="44" height="42" viewBox="0 0 44 42" fill="#444"><circle cx="9" cy="7" r="5"/><circle cx="35" cy="7" r="5"/><circle cx="22" cy="14" r="7"/><path d="M0 24c0-6 4-9 9-9s6 2 6 2c-3 2-4 5-4 8H0z"/><path d="M44 24c0-6-4-9-9-9s-6 2-6 2c3 2 4 5 4 8h11z"/><path d="M8 42V33c0-7 6-11 14-11s14 4 14 11v9z"/></svg>
    <ul>
      <li><svg width="9" height="9" viewBox="0 0 9 9"><rect x=".5" y="1.5" width="6.5" height="6.5" fill="none" stroke="#444"/><path d="M3 6l.5-2L8 .5l1 1-4.5 3.5z" fill="#444"/></svg>Lorem ipsum dolor sit amet, consectetur adipiscing elit, sed do eiusmod tempor incididunt labore et dolore magna aliqua.</li>
      <li><svg width="9" height="9" viewBox="0 0 9 9"><rect x=".5" y="1.5" width="6.5" height="6.5" fill="none" stroke="#444"/><path d="M3 6l.5-2L8 .5l1 1-4.5 3.5z" fill="#444"/></svg>Ut enim ad minim veniam quis nostrud exercitation ullamco laboris nisi ut aliquip ex ea commodo consequat.</li>
      <li><svg width="9" height="9" viewBox="0 0 9 9"><rect x=".5" y="1.5" width="6.5" height="6.5" fill="none" stroke="#444"/><path d="M3 6l.5-2L8 .5l1 1-4.5 3.5z" fill="#444"/></svg>Duis aute irure dolor in reprehenderit in voluptate velit esse cillum dolore eu pariatur.</li>
      <li><svg width="9" height="9" viewBox="0 0 9 9"><rect x=".5" y="1.5" width="6.5" height="6.5" fill="none" stroke="#444"/><path d="M3 6l.5-2L8 .5l1 1-4.5 3.5z" fill="#444"/></svg>Excepteur sint occaecat cupidatat non proident, sunt in culpa qui officia deserunt mollit est laborum.</li>
      <li><svg width="9" height="9" viewBox="0 0 9 9"><rect x=".5" y="1.5" width="6.5" height="6.5" fill="none" stroke="#444"/><path d="M3 6l.5-2L8 .5l1 1-4.5 3.5z" fill="#444"/></svg>Ut enim ad minim veniam quis nostrud exercitation ullamco laboris nisi ut aliquip ex ea commodo consequat.</li>
    </ul>
    <span class="more">READ MORE</span>
  </article>
  <article class="card right">
    <h3>Bank Lines Business</h3>
    <svg class="icon" width="30" height="42" viewBox="0 0 30 42" fill="#fff"><circle cx="15" cy="5" r="5"/><path d="M5 12h20a4 4 0 0 1 4 4v10a2 2 0 0 1-4 0V17h-1v23a2 2 0 0 1-4 0V28h-2v12a2 2 0 0 1-4 0V17H6v9a2 2 0 0 1-4 0V16a4 4 0 0 1 4-4z"/></svg>
    <ul>
      <li><svg width="9" height="9" viewBox="0 0 9 9"><rect x=".5" y="1.5" width="6.5" height="6.5" fill="none" stroke="#fff"/><path d="M3 6l.5-2L8 .5l1 1-4.5 3.5z" fill="#fff"/></svg>Lorem ipsum dolor sit amet, consectetur adipiscing elit, sed do eiusmod tempor incididunt labore et dolore magna aliqua.</li>
      <li><svg width="9" height="9" viewBox="0 0 9 9"><rect x=".5" y="1.5" width="6.5" height="6.5" fill="none" stroke="#fff"/><path d="M3 6l.5-2L8 .5l1 1-4.5 3.5z" fill="#fff"/></svg>Ut enim ad minim veniam quis nostrud exercitation ullamco laboris nisi ut aliquip ex ea commodo consequat.</li>
      <li><svg width="9" height="9" viewBox="0 0 9 9"><rect x=".5" y="1.5" width="6.5" height="6.5" fill="none" stroke="#fff"/><path d="M3 6l.5-2L8 .5l1 1-4.5 3.5z" fill="#fff"/></svg>Duis aute irure dolor in reprehenderit in voluptate velit esse cillum dolore eu pariatur.</li>
      <li><svg width="9" height="9" viewBox="0 0 9 9"><rect x=".5" y="1.5" width="6.5" height="6.5" fill="none" stroke="#fff"/><path d="M3 6l.5-2L8 .5l1 1-4.5 3.5z" fill="#fff"/></svg>Excepteur sint occaecat cupidatat non proident, sunt in culpa qui officia deserunt mollit est laborum.</li>
      <li><svg width="9" height="9" viewBox="0 0 9 9"><rect x=".5" y="1.5" width="6.5" height="6.5" fill="none" stroke="#fff"/><path d="M3 6l.5-2L8 .5l1 1-4.5 3.5z" fill="#fff"/></svg>Ut enim ad minim veniam quis nostrud exercitation ullamco laboris nisi ut aliquip ex ea commodo consequat.</li>
    </ul>
    <span class="more">READ MORE</span>
  </article>
</section>

<footer class="footer">
  <p>© All Rights Reserved. Copyrights @Company Name 2016</p>
  <div class="social" aria-label="Social links"><i></i><i></i><i></i><i></i><i></i></div>
</footer>
</body>
</html>
```